Letter and Envelope Design For Harborline Realty

Please design a letter and an envelope incorporating our logo (See Attached). We are also launched a business card contest. Since we want them to match, please feel free to submit a design for both the business card and also the letter design and envelope.

Requirements
Must have
• The envelope, the letter and the business cards must match somehow connecting the designs. We want them to have something that holds them together besides the logo.

```html
<!DOCTYPE html>
<html lang="en">
<head>
<meta charset="utf-8">
<title>Harborline Realty – Letterhead and Envelope</title>
<link href="https://fonts.googleapis.com/css2?family=Montserrat:wght@600&family=PT+Sans:wght@400;700&family=Arimo:wght@700&display=swap" rel="stylesheet">
<style>
  :root{
    --navy:#0a1a8a;
    --dark-gray:#555659;
    --light-gray:#b4b4b6;
    --text:#4a4a4c;
    --paper:#ffffff;
    --backdrop:#e6e6e8;
    --rule:#c9c9cc;
  }
  *{margin:0;padding:0;box-sizing:border-box}
  html,body{width:1200px;height:825px;overflow:hidden;background:var(--backdrop)}
  address{font-style:normal}
  .canvas{position:relative;width:1200px;height:825px}
  .sheet{position:absolute;background:var(--paper);overflow:hidden}
  .letter{left:80px;top:83px;width:465px;height:657px}
  .envelope-front{left:584px;top:250px;width:534px;height:232px}
  .envelope-back{left:584px;top:508px;width:534px;height:233px}

  .brand{position:absolute;text-align:center;color:var(--navy);font-family:"Montserrat",sans-serif;font-weight:600}
  .brand-mark{display:block;margin:0 auto 5px;width:44px;height:44px;border:2.5px solid var(--navy);border-radius:50%}
  .brand-name{display:block;font-size:12.5px;letter-spacing:1.6px;line-height:14px}
  .brand-sub{display:block;font-size:8px;letter-spacing:3px;line-height:11px}
  .letter .brand{left:34px;top:15px;width:116px}
  .envelope-front .brand{left:40px;top:16px;width:116px}

  .contact{position:absolute;left:338px;top:27px;font-family:"PT Sans",sans-serif;font-size:7.5px;color:var(--text);line-height:10px}
  .contact-row{display:flex;align-items:center;gap:4px}
  .contact-row svg{width:6px;height:6px;fill:var(--navy)}
  .contact-address{margin-top:6px}

  .greeting{position:absolute;left:36px;top:158px;font-family:"Arimo",sans-serif;font-weight:700;font-size:10.5px;color:#3c3c3e}
  .body{position:absolute;left:36px;top:186px;width:393px;font-family:"PT Sans",sans-serif;font-size:9.6px;line-height:12.2px;color:var(--text);text-align:justify}
  .body p{margin-bottom:12px}
  .signature{position:absolute;left:36px;top:456px;width:88px;height:42px;background:linear-gradient(90deg,#ececec,#f6f6f6);border-radius:4px}

  .swoosh{position:absolute;left:0;bottom:0;display:block}
  .web{position:absolute;font-family:"PT Sans",sans-serif;font-size:9.5px;letter-spacing:1px;color:#fff}
  .web b{font-weight:700}
  .letter .web{left:36px;bottom:11px}
  .envelope-front .web{left:42px;bottom:16px}

  .return-address{position:absolute;left:36px;top:88px;display:flex;gap:4px;font-family:"PT Sans",sans-serif;font-size:7.5px;line-height:10.5px;color:var(--text)}
  .return-address svg{width:8px;height:11px;fill:var(--navy)}

  .recipient{position:absolute;left:294px;top:100px;width:205px;height:65px;border:1px solid #f0f0f0;border-radius:6px;padding:6px 8px}
  .recipient-label{font-family:"PT Sans",sans-serif;font-size:7px;color:var(--text)}
  .recipient-line{border-bottom:1px dotted var(--rule);height:13px}
  .recipient-line:first-of-type{margin-top:-3px}

  .flap{position:absolute;left:0;top:0;width:534px;height:57px;border:1px solid #ececec;border-top:none;border-radius:0 0 22px 22px}
</style>
</head>
<body>
<main class="canvas">

  <article class="sheet letter">
    <div class="brand">
      <span class="brand-mark"></span>
      <span class="brand-name">HARBORLINE</span>
      <span class="brand-sub">REALTY</span>
    </div>

    <address class="contact">
      <div class="contact-row"><svg viewBox="0 0 10 10"><path d="M1 3q4-3 8 0l-1 2-2-1V3H4v1L2 5z"/><rect x="2" y="5" width="6" height="4" rx="1"/></svg>555-014-2210</div>
      <div class="contact-row"><svg viewBox="0 0 10 10"><rect x="0" y="2" width="10" height="6"/></svg>info@harborlinerealty.com</div>
      <div class="contact-address">Po. box 201, Street Name,<br>City Name, Zip Code - 00000</div>
    </address>

    <p class="greeting">Dear Mr. John,</p>
    <div class="body">
      <p>Lorem Ipsum is simply dummy text of the printing and typesetting industry. Lorem Ipsum has been the industry's standard dummy text ever since the 1500s, when an unknown printer took a galley of type and scrambled it to make a type specimen book. It has survived not only five centuries, but also the leap into electronic typesetting, remaining essentially unchanged.</p>
      <p>The standard chunk of Lorem Ipsum used since the 1500s is reproduced below for those interested. Sections 1.10.32 and 1.10.33 from "de Finibus Bonorum et Malorum" by Aurel Denmoor are also reproduced in their exact original form, accompanied by English versions from the 1914 translation by H. Lanford</p>
      <p>Lorem Ipsum is simply dummy text of the printing and typesetting industry. Lorem Ipsum has been the industry's standard dummy text ever since the 1500s, when an unknown printer took a galley of type and scrambled it to make a type specimen book. It has survived not only five centuries, but also the leap into electronic typesetting, remaining essentially unchanged. It was popularised in the</p>
      <p>Lorem Ipsum is simply dummy text of the printing and typesetting industry. Lorem Ipsum has been the industry's standard dummy text ever since the 1500s, when an unknown printer took a galley of type and scrambled it to make a type specimen book. It has survived not only five centuries, but also the leap into electronic typesetting, remaining essentially unchanged. It was popularised in the</p>
    </div>
    <div class="signature" role="img" aria-label="Handwritten signature of the sender"></div>

    <svg class="swoosh" width="465" height="80" viewBox="0 0 465 80" aria-hidden="true">
      <defs>
        <linearGradient id="band-letter" x1="0" x2="1" y1="0" y2="0">
          <stop offset="0.45" stop-color="#555659"/>
          <stop offset="0.72" stop-color="#b4b4b6"/>
        </linearGradient>
      </defs>
      <path d="M0,0 Q260,64 465,28 L465,37 Q260,74 0,11 Z" fill="url(#band-letter)"/>
      <path d="M0,16 Q260,80 465,42 L465,80 L0,80 Z" fill="var(--navy)"/>
    </svg>
    <p class="web">www.<b>harborlinerealty</b>.com</p>
  </article>

  <section class="sheet envelope-front">
    <div class="brand">
      <span class="brand-mark"></span>
      <span class="brand-name">HARBORLINE</span>
      <span class="brand-sub">REALTY</span>
    </div>
    <address class="return-address">
      <svg viewBox="0 0 8 11"><path d="M4 0a4 4 0 0 1 4 4c0 3-4 7-4 7S0 7 0 4a4 4 0 0 1 4-4zm0 2a2 2 0 1 0 0 4 2 2 0 0 0 0-4z"/></svg>
      <span>Po. box 201, Street Name,<br>City Name, Zip Code - 00000</span>
    </address>
    <div class="recipient">
      <div class="recipient-label">To</div>
      <div class="recipient-line"></div>
      <div class="recipient-line"></div>
      <div class="recipient-line"></div>
      <div class="recipient-line"></div>
    </div>
    <svg class="swoosh" width="534" height="92" viewBox="0 0 534 92" aria-hidden="true">
      <defs>
        <linearGradient id="band-envelope" x1="0" x2="1" y1="0" y2="0">
          <stop offset="0.45" stop-color="#555659"/>
          <stop offset="0.72" stop-color="#b4b4b6"/>
        </linearGradient>
      </defs>
      <path d="M0,4 Q300,80 534,38 L534,48 Q300,88 0,16 Z" fill="url(#band-envelope)"/>
      <path d="M0,22 Q300,96 534,54 L534,92 L0,92 Z" fill="var(--navy)"/>
    </svg>
    <p class="web">www.<b>harborlinerealty</b>.com</p>
  </section>

  <section class="sheet envelope-back">
    <div class="flap"></div>
  </section>

</main>
</body>
</html>
```